Home Remodeler Needs a Website!

Single page (plus contact form) website for small home remodeling company. He's got a few pictures he'd like on the site and needs some basic text. He likes clean, simple designs and is "more traditional" in his stylistic preferences. Most of his business comes from word-of-mouth advertising and so the site is just something he needs for people to feel more comfortable with his business.

Target Market(s)

People who want to remodel their homes

Coding

Coded - Design and coding required

Number of Pages Required

2 page

Requirements
Must have
• Main page to include some or all of the attached images, contact page. Neutral colors. Old domain: lindcroftmeadowbuild.com New domain: qm-ventureworks.com You can pull text from the old site or update it.
Should not have
• No loud colors/loud visual elements

```html
<!DOCTYPE html>
<html lang="en">
<head>
<meta charset="utf-8">
<title>Lindcroft Meadow Build — Home Remodeling</title>
<link rel="stylesheet" href="https://fonts.googleapis.com/css2?family=Mulish:wght@400;600;700;800&family=PT+Serif:ital,wght@1,700&family=Roboto+Slab:wght@400;500&display=swap">
<style>
:root{
  --teal:#0aaeb8;
  --ink:#1a1a1a;
  --text:#333;
  --muted:#9a9a9a;
  --line:#e2e2e2;
  --white:#fff;
  --black:#000;
  --overlay:rgba(20,24,30,.55);
}
*{box-sizing:border-box;margin:0;padding:0}
html,body{width:1200px;height:4040px;overflow:hidden}
body{position:relative;background:var(--white);font-family:'Mulish',sans-serif;color:var(--text)}
.abs{position:absolute}
.serif-head{font-family:'PT Serif',serif;font-style:italic;font-weight:700;color:var(--ink)}
.brand{font-family:'Roboto Slab',serif;font-weight:500;color:var(--teal);font-size:23px;line-height:29px}

/* header */
.site-header{left:0;top:0;width:1200px;height:86px;background:var(--white)}
.site-header .brand{left:110px;top:15px}
.main-nav{right:113px;top:31px;display:flex;gap:35px;font-size:15px;font-weight:700;color:var(--ink);letter-spacing:.3px}

/* hero */
.hero{left:0;top:86px;width:1200px;height:559px;background:linear-gradient(120deg,#5b5248 0%,#3c3a3a 35%,#6b6a6e 60%,#2e2b2a 100%)}
.hero::after{content:"";position:absolute;inset:0;background:rgba(0,0,0,.25)}
.hero-title{left:0;width:1200px;top:170px;text-align:center;font-family:'PT Serif',serif;font-style:italic;font-weight:700;color:var(--white);font-size:47px;line-height:58px;z-index:1}
.btn{display:flex;align-items:center;justify-content:center;background:var(--teal);color:var(--white);font-weight:700;font-size:15px;letter-spacing:.5px}
.hero .btn{position:absolute;left:519px;top:322px;width:162px;height:55px;z-index:1}

/* service tiles */
.tiles{left:107px;top:736px;width:986px;height:222px;background:var(--teal);display:flex}
.tile{flex:1;border-right:1px solid rgba(255,255,255,.35);position:relative;color:var(--white);text-align:center;font-weight:700;font-size:16px;line-height:22px}
.tile:last-child{border-right:0}
.tile svg{position:absolute;left:50%;top:30px;transform:translateX(-50%)}
.tile span{position:absolute;left:0;right:0;top:150px}

/* about */
.photo{display:block}
.about-photo{left:149px;top:1053px;width:433px;height:398px;background:linear-gradient(160deg,#6b4a36 0%,#3a2a22 45%,#141014 100%)}
.about-text{left:618px;top:1070px;width:420px}
.about-text h2{font-size:34px;line-height:40px;margin-bottom:14px}
.about-text h3{font-size:30px;line-height:36px;margin-bottom:20px}
.copy p{font-size:15px;line-height:24px;margin-bottom:24px;color:var(--text)}

/* services */
.services-head{left:177px;top:1572px;font-size:34px;line-height:42px;width:400px}
.services-copy{left:174px;top:1680px;width:420px}
.trades{left:140px;top:1949px;display:flex;gap:38px}
.trade{width:88px;text-align:center;font-size:15px;line-height:24px;color:var(--ink);font-weight:600}
.trade .avatar{width:88px;height:88px;border-radius:50%;margin-bottom:8px}
.trade span{display:block;white-space:nowrap;margin-left:-30px;margin-right:-30px}
.ba{left:692px;width:336px;height:291px}
.ba-before{top:1539px;background:linear-gradient(180deg,#cfccc6 0%,#e8e6e2 50%,#a9a6a2 100%)}
.ba-after{top:1829px;background:linear-gradient(180deg,#d9d5cf 0%,#6d7561 55%,#2c302c 100%)}
.ba-label{position:absolute;left:0;right:0;bottom:0;height:66px;background:rgba(30,32,36,.78);color:var(--white);font-size:29px;font-weight:700;text-align:center;line-height:66px}

/* video band */
.video-band{left:0;top:2206px;width:1200px;height:472px;background:linear-gradient(100deg,#4a4d52 0%,#6e7782 50%,#4d5157 100%)}
.video-band::after{content:"";position:absolute;inset:0;background:rgba(30,36,46,.35)}
.video-title{left:0;width:1200px;top:120px;text-align:center;color:var(--white);font-size:36px;line-height:44px;font-weight:400;z-index:1}
.play{left:531px;top:224px;z-index:1}

/* contact */
.contact-card{left:113px;top:2766px;width:974px;height:650px;background:var(--white);box-shadow:0 0 10px rgba(0,0,0,.15)}
.contact-media{position:absolute;left:0;top:0;width:488px;height:650px;background:linear-gradient(170deg,#3a3b3c 0%,#2a2a2a 50%,#191919 100%)}
.contact-media::after{content:"";position:absolute;inset:0;background:rgba(0,0,0,.35)}
.info{position:absolute;left:121px;color:var(--white);font-size:14px;line-height:24px;z-index:1}
.info b{font-weight:700}
.info .val{color:var(--teal);display:block}
.info .dim{color:#6c6c6c;display:block}
.info svg{position:absolute;left:-26px;top:4px}
.message-form{position:absolute;left:538px;top:0;width:388px}
.message-form h2{text-align:center;font-size:27px;font-weight:600;color:var(--ink);margin-top:40px;margin-bottom:28px}
.field{border:1px solid var(--line);margin-bottom:18px}
.field .label{height:47px;line-height:47px;padding-left:13px;font-size:14px;color:var(--ink);border-bottom:1px solid var(--line)}
.field .input{height:46px;line-height:46px;padding-left:17px;font-size:14px;color:var(--muted)}
.field .split{display:flex}
.field .split div{flex:1}
.field .split div+div{border-left:1px solid var(--line)}
.message-form .btn{width:188px;height:44px;margin:37px auto 0 115px}

/* footer */
.site-footer{left:0;top:3513px;width:1200px;height:527px;background:var(--black);color:var(--white)}
.site-footer .brand{position:absolute;left:177px;top:70px}
.divider{position:absolute;top:42px;width:1px;height:251px;background:#444}
.f-col{position:absolute;text-align:center;font-size:14px;line-height:24px}
.f-col h4{font-size:17px;font-weight:700;letter-spacing:.5px}
.news-input{position:absolute;left:457px;top:135px;width:291px;height:50px;background:var(--white);color:var(--ink);font-size:14px;text-align:center;line-height:50px}
.site-footer .sub{position:absolute;left:532px;top:204px;width:141px;height:49px}
.quick-title{position:absolute;left:0;width:1177px;text-align:center;top:325px;font-size:17px;font-weight:700}
.quick-links{position:absolute;left:0;width:1177px;top:381px;display:flex;justify-content:center;gap:31px;font-size:15px;font-weight:600}
.copyright{position:absolute;left:0;width:1200px;text-align:center;top:471px;font-size:14px}
</style>
</head>
<body>

<header class="site-header abs">
  <div class="brand abs">LINDCROFT MEADOW<br>BUILD</div>
  <nav class="main-nav abs">
    <span>HOME</span><span>ABOUT US</span><span>PRODUCTS</span><span>EXTRAS</span><span>RESOURCES</span><span>CONTACT US</span>
  </nav>
</header>

<section class="hero abs" role="img" aria-label="Photo of a remodeled kitchen with stainless refrigerator, sink and island">
  <h1 class="hero-title abs">WELCOME TO LINDCROFT<br>MEADOW BUILD</h1>
  <div class="btn">LEARN MORE</div>
</section>

<section class="tiles abs">
  <div class="tile">
    <svg width="80" height="80" viewBox="0 0 80 80" fill="none" stroke="#fff" stroke-width="2.5" stroke-linejoin="round"><rect x="12" y="22" width="48" height="36" rx="3"/><path d="M44 48 L66 14 L72 19 L50 52 L42 56 Z"/><path d="M8 46 L30 68 L36 62 L14 40 Z"/><path d="M18 50l4-4M23 55l4-4"/></svg>
    <span>Pre Construction<br>Consultation</span>
  </div>
  <div class="tile">
    <svg width="80" height="80" viewBox="0 0 80 80" fill="none" stroke="#fff" stroke-width="2.5" stroke-linejoin="round"><path d="M20 14 L30 24 L24 30 L14 20 A12 12 0 0 0 30 36 L58 64 L64 58 L36 30 A12 12 0 0 0 20 14 Z"/><path d="M64 14 L70 20 L40 50 L34 44 Z"/><path d="M34 44 L18 60 L24 66 L40 50"/></svg>
    <span>New Construction</span>
  </div>
  <div class="tile">
    <svg width="90" height="90" viewBox="0 0 90 90" fill="none" stroke="#fff" stroke-width="2.5"><rect x="8" y="8" width="22" height="18"/><rect x="36" y="8" width="16" height="14"/><rect x="58" y="8" width="22" height="18"/><rect x="8" y="44" width="74" height="38"/><path d="M8 58h74M30 44v38M56 44v38"/><rect x="14" y="32" width="14" height="12"/><circle cx="64" cy="52" r="3"/><circle cx="72" cy="52" r="3"/></svg>
    <span>Remodeling<br>kitchens and baths</span>
  </div>
  <div class="tile">
    <svg width="82" height="82" viewBox="0 0 82 82" fill="none" stroke="#fff" stroke-width="3"><circle cx="41" cy="41" r="37"/><path d="M41 22v38M22 41h38"/></svg>
    <span style="top:155px">Additions</span>
  </div>
  <div class="tile">
    <svg width="86" height="90" viewBox="0 0 86 90" fill="none" stroke="#fff" stroke-width="2.5"><path d="M6 86V8h74v78M6 14h74"/><path d="M22 14v22M64 14v22"/><rect x="16" y="36" width="54" height="24"/><path d="M24 36v24M32 36v24M40 36v24M48 36v24M56 36v24M62 36v24"/><path d="M12 60h62"/></svg>
    <span style="top:155px">Porches and Decks</span>
  </div>
</section>

<div class="about-photo photo abs" role="img" aria-label="Photo of a wooden kitchen with breakfast bar and pendant lights"></div>
<section class="about-text abs">
  <h2 class="serif-head">ABOUT US</h2>
  <h3 class="serif-head">DON'T TINKER AROUND</h3>
  <div class="copy">
    <p>I have built my business with a partnership of clients, employees, subcontractors, suppliers and inspectors. Since each project is unique, this partnership brings creative ideas to your home.</p>
    <p>I have deep "hands on" history in construction from foundations to final finishing touches.</p>
    <p>We cultivate suppliers who deliver quality materials on time and without damage.</p>
  </div>
</section>

<h2 class="services-head serif-head abs">PROVIDING SERVICES<br>FOR ROOFING</h2>
<div class="services-copy copy abs">
  <p>Lorem ipsum dolor sit amet, consectetur adipiscing elit, sed do eiusmod tempor incididunt ut labore et dolore magna aliqua. Ut enim ad minim veniam, quis nostrud exercitation</p>
  <p>Lorem ipsum dolor sit amet, consectetur adipiscing elit, sed do eiusmod tempor incididunt</p>
  <p>Lorem ipsum dolor sit amet, consectetur adipiscing elit, sed do eiusmod tempor incididunt</p>
</div>
<div class="trades abs">
  <div class="trade"><div class="avatar" role="img" aria-label="Photo of roofing work" style="background:radial-gradient(circle,#8a7a60,#3e4a5a)"></div><span>ROOFING</span></div>
  <div class="trade"><div class="avatar" role="img" aria-label="Photo of window replacement work" style="background:radial-gradient(circle,#9a8e88,#4a4440)"></div><span>WINDOW<br>REPLACEMENT</span></div>
  <div class="trade"><div class="avatar" role="img" aria-label="Photo of electrical work" style="background:radial-gradient(circle,#b07040,#3a2a20)"></div><span>ELECTRICAL</span></div>
  <div class="trade"><div class="avatar" role="img" aria-label="Photo of interior painting" style="background:radial-gradient(circle,#8fd0dc,#3a7f9a)"></div><span>PAINTING</span></div>
</div>
<div class="ba ba-before abs" role="img" aria-label="Bathroom before remodeling"><div class="ba-label">Before</div></div>
<div class="ba ba-after abs" role="img" aria-label="Bathroom after remodeling with green tile"><div class="ba-label">After</div></div>

<section class="video-band abs" role="img" aria-label="Photo of a remodeled bathroom with soaking tub">
  <h2 class="video-title abs">SED UT PERSPICIATIS<br>UNDE OMNIS</h2>
  <svg class="play abs" width="138" height="138" viewBox="0 0 138 138"><circle cx="69" cy="69" r="62" fill="none" stroke="rgba(255,255,255,.45)" stroke-width="1.5"/><circle cx="69" cy="69" r="39" fill="#0aaeb8"/><path d="M62 57 L80 69 L62 81 Z" fill="#fff"/></svg>
</section>

<section class="contact-card abs">
  <div class="contact-media" role="img" aria-label="Photo of a finished basement interior">
    <div class="info" style="top:214px">
      <svg width="12" height="14" viewBox="0 0 12 14"><path d="M6 0a5 5 0 0 0-5 5c0 4 5 9 5 9s5-5 5-9a5 5 0 0 0-5-5z" fill="#fff"/><circle cx="6" cy="5" r="2" fill="#2a2a2a"/></svg>
      <b>Address</b><span class="dim">Lorem ipsum dolor sit amet consectetur<br>adipiscing elit,</span>
    </div>
    <div class="info" style="top:310px">
      <svg width="13" height="13" viewBox="0 0 24 24"><path d="M6.6 10.8a15 15 0 0 0 6.6 6.6l2.2-2.2a1 1 0 0 1 1-.25 11 11 0 0 0 3.6.57 1 1 0 0 1 1 1V20a1 1 0 0 1-1 1A17 17 0 0 1 3 4a1 1 0 0 1 1-1h3.5a1 1 0 0 1 1 1 11 11 0 0 0 .57 3.6 1 1 0 0 1-.25 1z" fill="#fff"/></svg>
      <b>Phone</b><span class="val">888-888-8888</span>
    </div>
    <div class="info" style="top:389px">
      <svg width="15" height="12" viewBox="0 0 15 12" fill="none" stroke="#fff" stroke-width="1.5"><rect x="1" y="1" width="13" height="10"/><path d="M1 1l6.5 5.5L14 1"/></svg>
      <b>Email</b><span class="val">companyname@mailbox.com</span>
    </div>
  </div>
  <form class="message-form">
    <h2>Send Us A Message</h2>
    <div class="field"><div class="label">TELL US YOUR NAME</div><div class="split"><div class="input">First Name</div><div class="input">Last Name</div></div></div>
    <div class="field"><div class="label">ENTER YOUR EMAIL</div><div class="input">Eg.example@email.com</div></div>
    <div class="field"><div class="label">ENTER PHONE NUMBER</div><div class="input">Eg +1800 000000</div></div>
    <div class="field"><div class="label">MESSAGE</div><div class="input">Write Us a message</div></div>
    <div class="btn">SEND MESSAGE</div>
  </form>
</section>

<footer class="site-footer abs">
  <div class="brand">LINDCROFT MEADOW<br>BUILD</div>
  <div class="f-col" style="left:157px;width:220px;top:142px">Sed ut perspiciatis unde omnis iste natus error sit voluptatem accusantium doloremque laudantium, totam rem aperiam, eaque</div>
  <div class="divider" style="left:419px"></div>
  <div class="f-col" style="left:450px;width:300px;top:85px"><h4>NEWSLETTER</h4></div>
  <div class="news-input">Enter your email</div>
  <div class="btn sub">SUBSCRIBE</div>
  <div class="divider" style="left:789px"></div>
  <div class="f-col" style="left:780px;width:292px;top:82px">
    <h4>CONTACT INFO</h4>
    <div style="margin-top:14px">Sed ut perspiciatis unde<br>omnis iste natusiam</div>
    <div style="margin-top:16px">Call Us: 188-888-8888</div>
    <div style="margin-top:15px">Email Us: Support@lindcroftmeadow.com</div>
  </div>
  <div class="quick-title">QUICK LINKS</div>
  <nav class="quick-links"><span>HOME</span><span>ABOUT US</span><span>PRODUCTS</span><span>EXTRAS</span><span>RESOURCES</span><span>CONTACT US</span></nav>
  <div class="copyright">©Copyrights 2021 &nbsp;Home Remodeling &nbsp; | &nbsp; All Rights Reserved</div>
</footer>

</body>
</html>
```